High Tech Real Estate Startup needs a business card

We are developing an innovative real estate marketing product based around advanced search and virtual reality.

We talk to people, we need business cards.

Target Market(s)

The target market is technology professionals and realtors.

Contact Information for Business Card

The information to be included will include

Name
Title
Phone Number
E-mail Address
www.zelquin.com

It should use simple iconography for each one of those fields.

Font styles to use
Other font styles liked:
• Co, Jubilat, Avenir

Colors

Designer to choose colors to be used in the design.

Requirements
Must have
• Clean aesthetic,
• Good use of negative space.
• It should use our company logo, shown in the attached file. It is able to use the negative of that logo (coloured font and white background) and I have attached other acceptable accent colours in a swatch file.
Should not have
• Should not be too busy
• No extraneous text (slogans, tag lines etc)

```html
<!DOCTYPE html>
<html lang="en">
<head>
<meta charset="utf-8">
<title>Zelquin Business Card</title>
<link rel="stylesheet" href="https://fonts.googleapis.com/css2?family=Raleway:wght@400;600;700&display=swap">
<style>
  :root {
    --teal: #02b9bf;
    --paper: #ffffff;
    --ink: #3a3a3a;
    --muted: #6b6b6b;
    --backdrop: #e6e8e9;
  }
  * { box-sizing: border-box; margin: 0; padding: 0; }
  html, body { width: 1200px; height: 911px; overflow: hidden; }
  body {
    background: var(--backdrop);
    font-family: "Raleway", sans-serif;
    position: relative;
  }
  .card {
    position: absolute;
    left: 340px;
    width: 520px;
    height: 297px;
    box-shadow: 0 6px 18px rgba(0,0,0,0.18);
    overflow: hidden;
  }
  .card-front { top: 120px; background: var(--paper); }
  .card-back { top: 494px; background: var(--teal); display: flex; align-items: center; justify-content: center; }

  .wordmark {
    font-weight: 600;
    letter-spacing: 0.06em;
    line-height: 1;
  }
  .card-front .wordmark {
    position: absolute;
    top: 34px;
    right: 36px;
    font-size: 40px;
    color: var(--teal);
  }
  .card-back .wordmark {
    font-size: 62px;
    color: var(--paper);
  }

  .name-tab {
    position: absolute;
    left: 0;
    top: 184px;
    width: 12px;
    height: 30px;
    background: var(--teal);
    border-radius: 0 6px 6px 0;
  }
  .identity {
    position: absolute;
    left: 36px;
    top: 180px;
  }
  .person-name {
    font-size: 19px;
    font-weight: 700;
    color: var(--teal);
    letter-spacing: 0.02em;
  }
  .person-title {
    font-size: 13px;
    font-weight: 700;
    color: var(--ink);
    letter-spacing: 0.04em;
    margin-top: 2px;
  }
  .contact-list {
    list-style: none;
    margin-top: 12px;
  }
  .contact-item {
    display: flex;
    align-items: center;
    gap: 8px;
    font-size: 12px;
    color: var(--muted);
    line-height: 1.75;
  }
  .contact-icon { width: 11px; height: 11px; flex: none; }
</style>
</head>
<body>
  <section class="card card-front">
    <div class="wordmark">ZELQUIN</div>
    <span class="name-tab"></span>
    <div class="identity">
      <p class="person-name">DARA HOLT</p>
      <p class="person-title">CEO/FOUNDER</p>
      <ul class="contact-list">
        <li class="contact-item">
          <svg class="contact-icon" viewBox="0 0 12 12" aria-hidden="true"><path fill="#02b9bf" d="M2.4 1h2l1 2.6-1.3.9a6 6 0 0 0 3.4 3.4l.9-1.3 2.6 1v2c0 .8-.6 1.4-1.4 1.4A9.2 9.2 0 0 1 1 2.4C1 1.6 1.6 1 2.4 1z"/></svg>
          555 203 4187
        </li>
        <li class="contact-item">
          <svg class="contact-icon" viewBox="0 0 12 12" aria-hidden="true"><rect x="0.5" y="2" width="11" height="8" rx="1" fill="#02b9bf"/><path d="M1 2.6 6 6.6l5-4" stroke="#fff" stroke-width="1" fill="none"/></svg>
          dara@zelquin.com
        </li>
        <li class="contact-item">
          <svg class="contact-icon" viewBox="0 0 12 12" aria-hidden="true"><circle cx="6" cy="6" r="5.5" fill="#02b9bf"/><path d="M0.8 6h10.4M6 .6c-2.4 2.8-2.4 8 0 10.8M6 .6c2.4 2.8 2.4 8 0 10.8" stroke="#fff" stroke-width="0.8" fill="none"/></svg>
          www.zelquin.com
        </li>
      </ul>
    </div>
  </section>

  <section class="card card-back">
    <div class="wordmark">ZELQUIN</div>
  </section>
</body>
</html>
```